Wholesale in Gold Jewellery & Gold Bullion

We are an established gold jewellery and gold bullion wholesaler selling these products to international clients. We already have a name and logo of our company, hence please view attached current card design. We need a completely new design to compliment our business and industry and the final design should be new and elegant.

Contact Information for Business Card

New card details must be same as per current card. Like logo, name, tel no. & etc.

Colors

Designer to choose colors to be used in the design.

```html
<!DOCTYPE html>
<html lang="en">
<head>
<meta charset="utf-8">
<title>Aurelin &amp; Co – Business Card</title>
<link rel="stylesheet" href="https://fonts.googleapis.com/css2?family=Montserrat:wght@400;600&family=Tinos:wght@700&display=swap">
<style>
  :root {
    --backdrop: #2a2a2a;
    --card: #f3f3f3;
    --gold: #c98325;
    --ink: #1c1c1c;
    --muted: #4a4a4a;
  }
  * { margin: 0; padding: 0; box-sizing: border-box; }
  html, body {
    width: 1200px; height: 869px; overflow: hidden;
    background: var(--backdrop);
  }
  .card {
    position: absolute; left: 150px; top: 177px;
    width: 900px; height: 514px;
    background: var(--card);
    font-family: "Montserrat", sans-serif;
  }
  .brand {
    position: absolute; left: 170px; top: 112px;
    display: flex; align-items: center; gap: 42px;
  }
  .brand-dot {
    width: 110px; height: 110px; border-radius: 50%;
    background: var(--gold);
  }
  .brand-name {
    font-family: "Tinos", serif; font-weight: 700;
    font-size: 34px; color: var(--ink); letter-spacing: 0.5px;
  }
  .person {
    position: absolute; right: 455px; top: 278px;
    text-align: right;
  }
  .person-name {
    font-size: 34px; font-weight: 600; color: var(--gold);
    line-height: 1.1;
  }
  .person-role {
    font-size: 27px; font-weight: 400; color: var(--muted);
    line-height: 1.2;
  }
  .divider {
    position: absolute; left: 472px; top: 250px;
    width: 3px; height: 125px; background: var(--gold);
  }
  .contacts {
    position: absolute; left: 505px; top: 250px;
    list-style: none;
  }
  .contact {
    display: flex; align-items: center; gap: 18px;
    height: 32px;
    font-size: 20px; color: var(--muted);
  }
  .contact svg { width: 22px; height: 22px; fill: none; stroke: var(--gold); stroke-width: 2; }
  .contact svg.solid { fill: var(--gold); stroke: none; }
  .address {
    position: absolute; left: 0; right: 0; top: 432px;
    text-align: center; font-size: 21px; color: var(--muted);
  }
</style>
</head>
<body>
<main class="card">
  <div class="brand">
    <div class="brand-dot"></div>
    <div class="brand-name">AURELIN &amp; CO PTE LTD</div>
  </div>

  <div class="person">
    <div class="person-name">Ravin Solanki</div>
    <div class="person-role">Director</div>
  </div>

  <div class="divider"></div>

  <ul class="contacts">
    <li class="contact">
      <svg viewBox="0 0 24 24" aria-hidden="true"><rect x="7" y="2" width="10" height="20" rx="2"/><line x1="11" y1="18" x2="13" y2="18"/></svg>
      <span>+65 9100 2345</span>
    </li>
    <li class="contact">
      <svg viewBox="0 0 24 24" aria-hidden="true"><path d="M6 3l4 1-1 5-2 1c1 3 3 5 6 6l1-2 5-1 1 4c-1 3-4 4-7 3C8 19 5 16 4 11 3 7 4 4 6 3z"/></svg>
      <span>+65 6100 4000</span>
    </li>
    <li class="contact">
      <svg viewBox="0 0 24 24" aria-hidden="true"><rect x="7" y="3" width="10" height="7"/><rect x="3" y="10" width="18" height="10" rx="1"/><line x1="7" y1="15" x2="17" y2="15"/></svg>
      <span>+65 6100 4017</span>
    </li>
    <li class="contact">
      <svg class="solid" viewBox="0 0 24 24" aria-hidden="true"><path d="M2 5h20v2l-10 6L2 7z"/><path d="M2 9l10 6 10-6v10H2z"/></svg>
      <span>ravin@aurelinco.com</span>
    </li>
  </ul>

  <p class="address">12 Harlow Lane, Singapore 200118</p>
</main>
</body>
</html>
```